Business card for my new company (Accounting firm)

I need a business card for my new business Brightwell Advisory and Ledger SA. Our services are accounting, tax, audit and financial management. Our customers are small companies, start-ups and new companies. The final design has to show financial security, trust and growth. Please find our logo attached to the business card. Text for the business card: Brightwell Advisory and Ledger SA Tomas Varenholt Director and Founder Certified Accountant Tel. 022 418 57 34 tv@clairevalconseil.ch www.clairevalconseil.ch Rue des Vergières 27 1201 Geneva
Target Market(s)
Our customers are small companies, start-ups and new companies.
Industry/Entity Type
Finance And Accounting
Contact Information for Business Card
Claireval Conseil et Comptes SA
Tomas Varenholt
Directeur et Fondateur
Expert-comptable diplômé
Tél. 022 418 57 34
tv@clairevalconseil.ch
www.clairevalconseil.ch
Rue des Vergières 27
1201 Genève

```html
<!DOCTYPE html>
<html lang="fr">
<head>
<meta charset="utf-8">
<title>Claireval Conseil et Comptes SA – Cartes de visite</title>
<link rel="stylesheet" href="https://fonts.googleapis.com/css2?family=Roboto:wght@300;400;500;700&display=swap">
<style>
  :root {
    --bg: #2b2b2d;
    --navy: #1a6496;
    --deep: #1b5f95;
    --sky: #2aa9e0;
    --ink: #3a3a3c;
    --muted: #6d6e71;
    --rule: #a7a9ac;
    --paper: #ffffff;
  }
  * { margin: 0; padding: 0; box-sizing: border-box; }
  html, body { width: 1200px; height: 960px; overflow: hidden; }
  body {
    background: var(--bg);
    font-family: "Roboto", Arial, sans-serif;
    position: relative;
  }
  .card {
    position: absolute;
    width: 620px;
    height: 400px;
    overflow: hidden;
    box-shadow: 0 10px 30px rgba(0,0,0,.45);
  }

  /* Back side */
  .card-back {
    left: 50px; top: 60px;
    background: var(--navy);
    display: flex; flex-direction: column;
    align-items: center; justify-content: center;
    color: var(--paper);
  }
  .back-brand {
    display: flex; align-items: center; gap: 16px;
    font-size: 44px; font-weight: 500; letter-spacing: 3px;
  }
  .back-brand .mark {
    width: 34px; height: 34px; background: var(--sky);
  }
  .back-url {
    margin-top: 26px;
    font-size: 17px; font-weight: 300; letter-spacing: 3px;
  }

  /* Front side */
  .card-front {
    left: 530px; top: 500px;
    background: var(--paper);
  }
  .front-brand {
    position: absolute; right: 34px; top: 40px;
    text-align: right;
  }
  .front-brand .wordmark {
    display: flex; align-items: center; gap: 12px;
    font-size: 34px; font-weight: 500; letter-spacing: 2px;
    color: var(--ink);
  }
  .front-brand .wordmark .mark {
    width: 26px; height: 26px; background: var(--sky);
  }
  .front-brand .tagline {
    margin-top: 4px;
    font-size: 10.5px; letter-spacing: 2.2px;
    color: var(--muted); text-transform: uppercase;
  }
  .person {
    position: absolute; left: 40px; top: 186px;
  }
  .person .name {
    font-size: 27px; font-weight: 700; color: var(--sky);
  }
  .person .role {
    font-size: 15.5px; color: var(--ink); line-height: 1.3;
  }
  .divider {
    position: absolute; left: 40px; right: 30px; top: 262px;
    height: 1.5px; background: var(--rule);
  }
  .contact {
    position: absolute; left: 40px; top: 276px;
    list-style: none;
    font-size: 17px; color: var(--ink); line-height: 1.45;
  }
  .contact li { display: flex; align-items: center; gap: 10px; }
  .contact svg { width: 14px; height: 14px; fill: var(--sky); }
  .address {
    position: absolute; right: 34px; top: 276px;
    text-align: right; font-size: 15.5px; color: var(--ink); line-height: 1.3;
  }
  .footer-band {
    position: absolute; left: 0; bottom: 0; width: 620px; height: 70px;
  }
  .website {
    position: absolute; right: 28px; bottom: 20px;
    font-size: 17px; color: var(--paper); letter-spacing: .5px;
  }
</style>
</head>
<body>

  <section class="card card-back" aria-label="Verso de la carte">
    <div class="back-brand"><span class="mark"></span>CLAIREVAL</div>
    <div class="back-url">www.clairevalconseil.ch</div>
  </section>

  <section class="card card-front" aria-label="Recto de la carte">
    <div class="front-brand">
      <div class="wordmark"><span class="mark"></span>CLAIREVAL</div>
      <div class="tagline">Conseil et Comptes</div>
    </div>

    <div class="person">
      <div class="name">Tomas Varenholt</div>
      <div class="role">Directeur et Fondateur<br>Expert-comptable diplômé</div>
    </div>

    <div class="divider"></div>

    <ul class="contact">
      <li>
        <svg viewBox="0 0 24 24" aria-hidden="true"><path d="M6.6 10.8a15.1 15.1 0 0 0 6.6 6.6l2.2-2.2c.3-.3.7-.4 1-.2 1.1.4 2.3.6 3.6.6.6 0 1 .4 1 1V20c0 .6-.4 1-1 1A17 17 0 0 1 3 4c0-.6.4-1 1-1h3.5c.6 0 1 .4 1 1 0 1.3.2 2.5.6 3.6.1.3 0 .7-.2 1z"/></svg>
        022 418 57 34
      </li>
      <li>
        <svg viewBox="0 0 24 24" aria-hidden="true"><path d="M2 5h20v14H2zm2 2v.5l8 5 8-5V7l-8 5z"/></svg>
        tv@clairevalconseil.ch
      </li>
    </ul>

    <div class="address">Rue des Vergières 27<br>1201 Genève</div>

    <svg class="footer-band" viewBox="0 0 620 70" aria-hidden="true">
      <path d="M0 54 C160 50 300 42 370 32 C392 18 410 12 440 12 L620 12" fill="none" stroke="var(--sky)" stroke-width="3"/>
      <path d="M0 58 C160 55 300 48 372 38 C395 22 412 18 444 18 L620 18 L620 70 L0 70 Z" fill="var(--deep)"/>
      <path d="M0 62 C160 59 300 54 372 46" fill="none" stroke="var(--paper)" stroke-width="1.5" opacity=".7"/>
    </svg>
    <div class="website">www.clairevalconseil.ch</div>
  </section>

</body>
</html>
```